Spring Detox sale graphics for social media

You MUST read the Brief in the WORD document and follow the instructions there. I want to create 10 social media graphics (new Instagram size 4:5 (1080 x 1350 pixels) focusing on our Mother’s Day Spring Detox Sale graphics, using any of the pics attached. Use the attached pics, NO RANDOM STOCK PHOTOGRAPHY. For the color scheme of the graphics, they should all be complementary to the product colors or feel like Spring time.

Target Market(s)

primarily women

Requirements
Must have
• the photos and text attached

```html
<!DOCTYPE html>
<html lang="en">
<head>
<meta charset="utf-8">
<title>Spring Detox Sale</title>
<link rel="stylesheet" href="https://fonts.googleapis.com/css2?family=Oswald:wght@600;700&family=Yellowtail&display=swap">
<style>
  :root {
    --paper-edge: #fdf6ea;
    --cream: #f6e4bb;
    --card-white: #ffffff;
    --grid-cream: #f7e3b9;
    --rust: #d4623d;
    --forest: #536f31;
    --bottle-white: #eeeeec;
    --bottle-shade: #d9d8d4;
  }
  * { margin: 0; padding: 0; box-sizing: border-box; }
  html, body { width: 960px; height: 1200px; overflow: hidden; background: var(--paper-edge); }
  .poster { position: relative; width: 960px; height: 1200px; background: var(--paper-edge); }
  .leaf-backdrop {
    position: absolute; left: 18px; top: 18px; width: 924px; height: 1164px;
    background:
      radial-gradient(circle at 12% 20%, rgba(199,90,56,.35), transparent 28%),
      radial-gradient(circle at 90% 30%, rgba(228,154,130,.35), transparent 26%),
      radial-gradient(circle at 8% 70%, rgba(199,90,56,.3), transparent 26%),
      radial-gradient(circle at 92% 78%, rgba(199,90,56,.32), transparent 26%),
      radial-gradient(circle at 50% 98%, rgba(199,90,56,.28), transparent 24%),
      var(--cream);
  }
  .card {
    position: absolute; left: 99px; top: 91px; width: 762px; height: 1018px;
    background: var(--card-white);
    box-shadow: 0 10px 30px rgba(90,60,30,.35);
  }
  .card-inner {
    position: absolute; left: 11px; top: 11px; right: 11px; bottom: 11px;
    background: var(--grid-cream);
    overflow: hidden;
  }
  .headline {
    position: absolute; left: 0; width: 100%; text-align: center; white-space: nowrap;
    font-family: "Oswald", sans-serif; font-weight: 700; color: var(--rust);
    text-transform: uppercase; line-height: 1;
  }
  .headline-discount { top: 48px; font-size: 176px; letter-spacing: 2px; transform: scale(0.72, 1.03); }
  .headline-range { top: 225px; font-size: 98px; letter-spacing: -1px; transform: translateX(-31px) scaleX(0.8); }
  .sparkle { position: absolute; }
  .sparkle-rust { left: 640px; top: 251px; width: 73px; height: 73px; }
  .sparkle-forest { left: 510px; top: 381px; width: 62px; height: 62px; }
  .season-script {
    position: absolute; left: 0; top: 370px; width: 100%; text-align: center;
    font-family: "Yellowtail", cursive; font-size: 150px; color: var(--rust); line-height: 1;
    transform: translateX(-10px);
  }
  .ribbon { position: absolute; left: 149px; top: 545px; width: 440px; height: 98px; }
  .ribbon-label {
    position: absolute; left: 149px; top: 545px; width: 440px; height: 98px;
    display: flex; align-items: center; justify-content: center;
    font-family: "Oswald", sans-serif; font-weight: 700; font-size: 68px;
    color: var(--card-white); letter-spacing: 1px;
  }
  .bottle {
    position: absolute; border-radius: 22px 22px 14px 14px;
    background: linear-gradient(90deg, var(--bottle-shade), var(--bottle-white) 30%, var(--bottle-white) 70%, var(--bottle-shade));
    box-shadow: 0 6px 10px rgba(90,60,30,.3);
  }
  .bottle-liver { left: 88px; top: 674px; width: 133px; height: 237px; }
  .bottle-tummy { left: 240px; top: 677px; width: 120px; height: 234px; }
  .bottle-hormone { left: 384px; top: 677px; width: 122px; height: 234px; }
  .bottle-sugar { left: 540px; top: 685px; width: 110px; height: 226px; }
</style>
</head>
<body>
<main class="poster">
  <div class="leaf-backdrop" role="img" aria-label="Scattered terracotta spring leaves around the border"></div>
  <section class="card">
    <div class="card-inner">
      <h1 class="headline headline-discount">25% Off</h1>
      <p class="headline headline-range">All Supplements</p>
      <svg class="sparkle sparkle-rust" viewBox="0 0 82 82" aria-hidden="true">
        <path fill="#d4623d" d="M30 10 C33 32 38 38 58 42 C38 46 33 52 30 76 C27 52 22 46 2 42 C22 38 27 32 30 10Z"/>
        <path fill="#d4623d" d="M66 0 C67 10 70 13 78 14 C70 15 67 18 66 28 C65 18 62 15 54 14 C62 13 65 10 66 0Z"/>
        <path fill="#d4623d" d="M64 48 C65 58 68 61 76 62 C68 63 65 66 64 76 C63 66 60 63 52 62 C60 61 63 58 64 48Z"/>
      </svg>
      <p class="season-script">Spring</p>
      <svg class="sparkle sparkle-forest" viewBox="0 0 66 66" aria-hidden="true">
        <path fill="#536f31" d="M22 6 C24 26 28 30 44 32 C28 34 24 40 22 60 C20 40 16 34 0 32 C16 30 20 26 22 6Z"/>
        <path fill="#536f31" d="M52 0 C53 9 55 11 62 12 C55 13 53 15 52 24 C51 15 49 13 42 12 C49 11 51 9 52 0Z"/>
        <path fill="#536f31" d="M48 34 C49 42 51 44 58 45 C51 46 49 48 48 56 C47 48 45 46 38 45 C45 44 47 42 48 34Z"/>
      </svg>
      <svg class="ribbon" viewBox="0 0 440 98" aria-hidden="true">
        <polygon fill="#536f31" points="0,0 440,0 410,49 440,98 0,98 30,49"/>
      </svg>
      <p class="ribbon-label">DETOX SALE</p>
      <div class="bottle bottle-liver" role="img" aria-label="Liver support supplement bottle with pink label"></div>
      <div class="bottle bottle-tummy" role="img" aria-label="Digestive supplement bottle with red label"></div>
      <div class="bottle bottle-hormone" role="img" aria-label="Hormone balance supplement bottle with green label"></div>
      <div class="bottle bottle-sugar" role="img" aria-label="Blood sugar supplement bottle with blue label"></div>
    </div>
  </section>
</main>
</body>
</html>
```